Modern looking signage for dental office.

Exterior signage for passing cars
Updates
Need extra days to review
Target Market(s)
Cars passing by
Font styles to use
Sans Serif
Colors
3276b5
Requirements
Must have
- Logo
- OPEN ON SUTURDAY AND SUNDAY
- NIGHT CLINIC AVAILABLE
- PLEASE USE THE FONT TYPE IN FILE 4 UPLOADED BELOW.
- (847) 302-7469
- Modern looking

```html
<!DOCTYPE html>
<html lang="en">
<head>
<meta charset="utf-8">
<title>Arc Dental – Weekend &amp; Night Clinic Sign</title>
<link rel="stylesheet" href="https://fonts.googleapis.com/css2?family=Montserrat:ital,wght@0,400;0,700;1,400&family=Encode+Sans+Condensed:wght@400&display=swap">
<style>
  :root {
    --ink-grey: #5a5456;
    --navy: #1f2259;
    --mauve: #a6708e;
    --paper: #ffffff;
    --text-light: #ffffff;
  }
  html, body {
    margin: 0;
    padding: 0;
    width: 1200px;
    height: 1200px;
    overflow: hidden;
    background: var(--paper);
  }
  .sign {
    position: relative;
    width: 1200px;
    height: 1200px;
    background: var(--paper);
    font-family: "Montserrat", sans-serif;
    overflow: hidden;
  }
  .sign__shapes {
    position: absolute;
    inset: 0;
  }
  .brand__ring {
    position: absolute;
    left: 70px;
    top: 90px;
    width: 232px;
    height: 232px;
  }
  .brand__name {
    position: absolute;
    left: 322px;
    top: 160px;
    margin: 0;
    font-family: "Montserrat", sans-serif;
    font-weight: 400;
    font-size: 112px;
    line-height: 1;
    letter-spacing: 4px;
    color: var(--ink-grey);
    white-space: nowrap;
  }
  .brand__tagline {
    position: absolute;
    left: 402px;
    top: 282px;
    margin: 0;
    font-family: "Encode Sans Condensed", sans-serif;
    font-weight: 400;
    font-size: 50px;
    line-height: 1;
    color: var(--ink-grey);
    white-space: nowrap;
  }
  .line {
    position: absolute;
    left: 122px;
    margin: 0;
    line-height: 1;
    color: var(--text-light);
    white-space: nowrap;
  }
  .headline { font-size: 84px; font-weight: 400; }
  .headline--open { top: 480px; }
  .headline--days { top: 564px; font-size: 76px; top: 571px; }
  .detail { font-size: 46px; font-weight: 400; }
  .detail--night { top: 760px; }
  .detail--available { top: 820px; }
  .call__label { top: 986px; font-size: 46px; font-style: italic; }
  .call__number {
    top: 1051px;
    left: 208px;
    font-size: 66px;
    font-weight: 700;
    letter-spacing: 3px;
  }
  .call__icon {
    position: absolute;
    left: 118px;
    top: 1058px;
    width: 58px;
    height: 58px;
  }
</style>
</head>
<body>
<main class="sign">
  <svg class="sign__shapes" width="1200" height="1200" viewBox="0 0 1200 1200" aria-hidden="true">
    <path class="band band--mauve" fill="var(--mauve)"
      d="M1098 410 L1200 410 L1200 1200 L800 1200 C1050 1080 1140 850 1136 632 C1134 540 1120 470 1098 410 Z"/>
    <path class="band band--navy" fill="var(--navy)"
      d="M0 410 L1022 410 C1050 480 1066 560 1066 632 C1066 900 880 1140 496 1200 L0 1200 Z"/>
  </svg>

  <header class="brand">
    <svg class="brand__ring" viewBox="0 0 232 232" aria-hidden="true">
      <circle cx="116" cy="116" r="114" fill="none" stroke="var(--ink-grey)" stroke-width="3"/>
    </svg>
    <h1 class="brand__name">ARC DENTAL</h1>
    <p class="brand__tagline">MODERN GENERAL DENTISTRY</p>
  </header>

  <section class="hours">
    <p class="line headline headline--open">Open on</p>
    <p class="line headline headline--days">Saturday &amp; Sunday</p>
    <p class="line detail detail--night">Night clinic from 5pm to 10pm</p>
    <p class="line detail detail--available">AVAILABLE</p>
  </section>

  <section class="call">
    <p class="line call__label">Call</p>
    <svg class="call__icon" viewBox="0 0 24 24" aria-hidden="true">
      <path fill="var(--text-light)" d="M6.6 10.8c1.4 2.8 3.8 5.1 6.6 6.6l2.2-2.2c.3-.3.7-.4 1-.2 1.1.4 2.3.6 3.6.6.6 0 1 .4 1 1V20c0 .6-.4 1-1 1C10.6 21 3 13.4 3 4c0-.6.4-1 1-1h3.5c.6 0 1 .4 1 1 0 1.3.2 2.5.6 3.6.1.3 0 .7-.2 1z"/>
      <path fill="none" stroke="var(--text-light)" stroke-width="1.6" stroke-linecap="round" d="M14 6.5a4 4 0 0 1 3.5 3.5M14 3a7.5 7.5 0 0 1 7 7"/>
    </svg>
    <p class="line call__number">847-302-7469</p>
  </section>
</main>
</body>
</html>
```